Coffeeshop menu for filter tip

We want to have a cannabis (coffeeshop) menu in the size 25mm wide x 60mm wide. Some examples attached.

it must have the following text:
Menu

WEED p/g
Oblivane €16
Cloudplum €14
Tide Runner €14
Quincefig €16
Mega Marsh €14
Grey Heron €14

HASH p/g
Tashar Amber €12
Pebble Frost€11
Lime Dunes €14
Ash Petal €10

Target Market(s)

tourist in Amsterdam

Requirements
Nice to have
• cannabis sign leaf
• No Cigarettes allowed symbol

```html
<!DOCTYPE html>
<html lang="en">
<head>
<meta charset="utf-8">
<title>Coffeeshop Menu – Pure Retro</title>
<link href="https://fonts.googleapis.com/css2?family=Fira+Sans+Extra+Condensed:wght@400&family=Noto+Serif:wght@400;700&family=Roboto:wght@700&display=swap" rel="stylesheet">
<style>
  :root {
    --page: #fdfdfd;
    --ink: #1e1e1e;
    --label: #4a4a4a;
    --panel: #e4e4e4;
    --panel-edge: #d6d6d6;
    --frame: #3a3a3a;
    --header-bg: #2f2f2f;
    --header-fg: #ffffff;
    --orange: #f29a1c;
    --sign-red: #e0141b;
  }
  * { box-sizing: border-box; margin: 0; padding: 0; }
  html, body { width: 1200px; height: 780px; overflow: hidden; background: var(--page); }
  .canvas { position: relative; width: 1200px; height: 780px; }

  .variant-tag {
    position: absolute; left: 50px; top: 62px;
    font: 700 25px "Roboto", Arial, sans-serif; color: var(--label);
  }

  /* Side badge variants */
  .badge {
    position: absolute; width: 212px; height: 180px;
    display: flex; align-items: center; justify-content: center;
  }
  .badge--color { left: 126px; top: 254px; }
  .badge--mono  { left: 862px; top: 254px; }
  .badge-mark { position: absolute; inset: 0; }
  .badge-name {
    position: relative; text-align: center; line-height: 1.3;
    font: 700 15px "Noto Serif", Georgia, serif; letter-spacing: 1px;
    white-space: nowrap;
  }
  .badge--color .badge-name { color: var(--orange); }
  .badge--mono .badge-name { color: var(--ink); }

  /* Menu panel */
  .menu {
    position: absolute; left: 464px; top: 29px; width: 272px; height: 652px;
    background: var(--panel); border: 1px solid var(--panel-edge);
  }
  .menu-pattern { position: absolute; inset: 0; background: linear-gradient(180deg, #e6e6e6, #dcdcdc 50%, #e6e6e6); }
  .menu-frame {
    position: absolute; left: 12px; top: 12px; right: 12px; bottom: 12px;
    border: 1px solid var(--frame);
  }
  .corner { position: absolute; width: 28px; height: 26px; background: var(--ink); }
  .corner--tl { left: 12px; top: 12px; border-bottom-right-radius: 100% 100%; }
  .corner--tr { right: 12px; top: 12px; border-bottom-left-radius: 100% 100%; }
  .corner--bl { left: 12px; bottom: 12px; border-top-right-radius: 100% 100%; }
  .corner--br { right: 12px; bottom: 12px; border-top-left-radius: 100% 100%; }

  .section-title {
    position: absolute; height: 31px;
    background: var(--header-bg); color: var(--header-fg);
    border: 2px solid var(--header-bg); outline: 1px solid #9a9a9a; outline-offset: -4px;
    border-radius: 3px;
    display: flex; align-items: center; justify-content: center;
    font: 700 24px "Noto Serif", Georgia, serif; letter-spacing: 0.5px;
  }
  .section-title sup { font-size: 12px; font-weight: 400; margin-left: 6px; position: relative; top: -5px; }
  .section-title--weed { left: 66px; top: 34px; width: 144px; }
  .section-title--hash { left: 62px; top: 430px; width: 144px; }

  .price-list { position: absolute; left: 20px; width: 230px; list-style: none; }
  .price-list--weed { top: 69px; }
  .price-list--hash { top: 465px; }
  .price-row {
    display: flex; justify-content: space-between; align-items: baseline;
    border-bottom: 1.5px solid var(--ink);
    padding: 0 4px 0 8px; color: var(--ink);
  }
  .price-list--weed .price-row { height: 28.5px; }
  .price-list--hash .price-row { height: 29px; padding-right: 6px; }
  .price-list--hash .price-row:last-child { border-bottom: none; }
  .item-name { font: 400 20px "Fira Sans Extra Condensed", "Arial Narrow", sans-serif; }
  .item-price { font: 400 22px "Noto Serif", Georgia, serif; }
  .item-price .currency { font-size: 15px; margin-right: 5px; }

  .menu-emblem {
    position: absolute; left: 54px; top: 254px; width: 164px; height: 150px;
    display: flex; align-items: center; justify-content: center;
  }
  .menu-emblem svg { position: absolute; inset: 0; }
  .menu-emblem .badge-name { color: var(--ink); font-size: 13px; }

  .no-smoking { position: absolute; left: 106px; top: 584px; width: 60px; height: 38px; }
  .no-smoking-label {
    position: absolute; left: 0; right: 0; top: 622px; text-align: center;
    font: 700 11px "Noto Serif", Georgia, serif; letter-spacing: 1px; color: var(--ink);
  }
</style>
</head>
<body>
<div class="canvas">
  <p class="variant-tag">#new4-pure-retro</p>

  <div class="badge badge--color">
    <svg class="badge-mark" viewBox="0 0 212 180" aria-hidden="true">
      <circle cx="106" cy="90" r="76" fill="#ffffff" stroke="var(--ink)" stroke-width="3"/>
    </svg>
    <p class="badge-name">CANAL LEAF<br>MENU</p>
  </div>

  <section class="menu" aria-label="Coffeeshop price menu">
    <div class="menu-pattern" role="img" aria-label="Soft grey damask background pattern"></div>
    <div class="menu-frame"></div>
    <span class="corner corner--tl"></span>
    <span class="corner corner--tr"></span>
    <span class="corner corner--bl"></span>
    <span class="corner corner--br"></span>

    <h2 class="section-title section-title--weed">WEED<sup>p/g</sup></h2>
    <ul class="price-list price-list--weed">
      <li class="price-row"><span class="item-name">Oblivane</span><span class="item-price"><span class="currency">€</span>16</span></li>
      <li class="price-row"><span class="item-name">Cloudplum</span><span class="item-price"><span class="currency">€</span>16</span></li>
      <li class="price-row"><span class="item-name">Tide Runner</span><span class="item-price"><span class="currency">€</span>14</span></li>
      <li class="price-row"><span class="item-name">Quincefig</span><span class="item-price"><span class="currency">€</span>16</span></li>
      <li class="price-row"><span class="item-name">Mega Marsh</span><span class="item-price"><span class="currency">€</span>14</span></li>
      <li class="price-row"><span class="item-name">Grey Heron</span><span class="item-price"><span class="currency">€</span>14</span></li>
    </ul>

    <div class="menu-emblem">
      <svg viewBox="0 0 164 150" aria-hidden="true">
        <circle cx="82" cy="75" r="64" fill="#ffffff" stroke="var(--ink)" stroke-width="3"/>
      </svg>
      <p class="badge-name">CANAL LEAF<br>MENU</p>
    </div>

    <h2 class="section-title section-title--hash">HASH<sup>p/g</sup></h2>
    <ul class="price-list price-list--hash">
      <li class="price-row"><span class="item-name">Tashar Amber</span><span class="item-price"><span class="currency">€</span>12</span></li>
      <li class="price-row"><span class="item-name">Pebble Frost</span><span class="item-price"><span class="currency">€</span>11</span></li>
      <li class="price-row"><span class="item-name">Lime Dunes</span><span class="item-price"><span class="currency">€</span>14</span></li>
      <li class="price-row"><span class="item-name">Ash Petal</span><span class="item-price"><span class="currency">€</span>10</span></li>
    </ul>

    <svg class="no-smoking" viewBox="0 0 60 42" role="img" aria-label="No cigarettes sign">
      <path d="M6 4 q6 2 8 8" fill="none" stroke="var(--ink)" stroke-width="1.2"/>
      <circle cx="34" cy="21" r="18" fill="#ffffff" stroke="var(--sign-red)" stroke-width="4"/>
      <rect x="20" y="19" width="24" height="5" fill="var(--ink)"/>
      <rect x="44" y="19" width="5" height="5" fill="var(--orange)"/>
      <line x1="22" y1="9" x2="46" y2="33" stroke="var(--sign-red)" stroke-width="4"/>
    </svg>
    <p class="no-smoking-label">NO SIGARETS</p>
  </section>

  <div class="badge badge--mono">
    <svg class="badge-mark" viewBox="0 0 212 180" aria-hidden="true">
      <circle cx="106" cy="90" r="76" fill="#ffffff" stroke="var(--orange)" stroke-width="3"/>
    </svg>
    <p class="badge-name">CANAL LEAF<br>MENU</p>
  </div>
</div>
</body>
</html>
```